New Business Card for Software Company

We are looking at rebranding a 10 year old company that specializes in PDF and DWF solutions for Architects and Engineers. We will attach the new company logo that we are going with so you can work with that and complimentary colors.
The sample information we would like on the business card is:
Gerald Pinfold
Vice President
4738 W. Harrowgate Lane. STE 305
PMB#417
Mesa, AZ 85374
866-392-5074 US Toll Free
123-456-3190 Cell
gpinfold@plavorix.com
The old tag line that we had on the business cars was.
Providing Industrial Strength PDF and DWF Solutions to the Global CAD Marketplace.
If you have an idea for a better tag line we are open to that also.
Updates
We would like to thank all of the Designers for their wonderful work. We apologize that we will not have the time to provide feedback to everyone. There is just so many innovative and professional designs that you have all created making our decision even harder.
Target Market(s)
Architects and Engineers
Industry/Entity Type
Business
Look and feel

```html
<!DOCTYPE html>
<html lang="en">
<head>
<meta charset="utf-8">
<title>Plavorix Business Card</title>
<link href="https://fonts.googleapis.com/css2?family=Open+Sans:wght@400;600;800&display=swap" rel="stylesheet">
<style>
  :root {
    --page-bg: #e9e9ee;
    --card-white: #ffffff;
    --slate: #5f5f5f;
    --slate-dark: #4a4a4a;
    --orange: #f15a22;
    --orange-light: #f7941d;
    --orange-deep: #e0401f;
    --text-light: #ffffff;
    --text-soft: #e6e6e6;
  }
  * { margin: 0; padding: 0; box-sizing: border-box; }
  html, body { width: 1200px; height: 987px; overflow: hidden; }
  body {
    background: var(--page-bg);
    font-family: "Open Sans", Arial, sans-serif;
    position: relative;
  }
  .card {
    position: absolute;
    width: 560px;
    height: 320px;
    border-radius: 26px;
    overflow: hidden;
    box-shadow: 0 6px 18px rgba(0,0,0,0.15);
  }
  /* Back side */
  .card-back {
    left: 590px;
    top: 110px;
    background: var(--slate);
  }
  .card-back .brand-mark {
    position: absolute;
    left: 0; right: 0;
    top: 70px;
    display: flex;
    align-items: center;
    justify-content: center;
    gap: 14px;
  }
  .brand-dot {
    width: 46px; height: 46px;
    border-radius: 50%;
    background: var(--orange);
  }
  .card-back .brand-name {
    font-size: 54px;
    font-weight: 800;
    color: var(--orange);
    letter-spacing: -1px;
  }
  .tagline {
    position: absolute;
    left: 0; right: 0;
    top: 190px;
    text-align: center;
    color: var(--text-soft);
    font-size: 19px;
    line-height: 1.35;
  }
  /* Front side */
  .card-front {
    left: 50px;
    top: 520px;
    background: var(--card-white);
  }
  .card-front .bands { position: absolute; inset: 0; }
  .front-brand {
    position: absolute;
    left: 150px;
    top: 26px;
    font-size: 64px;
    font-weight: 800;
    color: var(--slate-dark);
    letter-spacing: -2px;
    line-height: 1;
  }
  .person {
    position: absolute;
    left: 258px;
    top: 108px;
    font-size: 16px;
    color: var(--slate);
    white-space: nowrap;
  }
  .person .person-name { color: var(--orange); font-weight: 800; }
  .address {
    position: absolute;
    left: 150px;
    top: 200px;
    color: var(--text-light);
    font-size: 15px;
    line-height: 1.4;
    white-space: nowrap;
  }
  .contact {
    position: absolute;
    left: 22px;
    top: 268px;
    color: var(--text-light);
    font-size: 14.5px;
    display: flex;
    align-items: center;
    gap: 6px;
    white-space: nowrap;
  }
  .contact svg { width: 13px; height: 13px; fill: var(--text-light); flex: none; }
  .contact .sep { width: 8px; }
</style>
</head>
<body>

  <section class="card card-back" aria-label="Card back">
    <div class="brand-mark">
      <span class="brand-dot"></span>
      <span class="brand-name">plavorix</span>
    </div>
    <p class="tagline">Providing Industrial Strength PDF and<br>DWF Solutions to the Global CAD Marketplace</p>
  </section>

  <section class="card card-front" aria-label="Card front">
    <svg class="bands" viewBox="0 0 560 320" preserveAspectRatio="none" aria-hidden="true">
      <defs>
        <linearGradient id="orangeFill" x1="0" y1="1" x2="1" y2="0">
          <stop offset="0" stop-color="var(--orange-deep)"/>
          <stop offset="0.6" stop-color="var(--orange)"/>
          <stop offset="1" stop-color="var(--orange-light)"/>
        </linearGradient>
      </defs>
      <path d="M0 80 C 150 150, 350 175, 560 165 L560 320 L0 320 Z" fill="var(--slate)"/>
      <path d="M0 98 C 150 168, 350 193, 560 183 L560 320 L0 320 Z" fill="url(#orangeFill)"/>
    </svg>

    <div class="front-brand">plavorix</div>
    <p class="person"><span class="person-name">Gerald Pinfold,</span> Vice President</p>
    <p class="address">4738 W. Harrowgate Lane. STE 305<br>PMB#417, Mesa, AZ 85374</p>
    <p class="contact">
      <svg viewBox="0 0 24 24" aria-hidden="true"><path d="M6.6 10.8a15 15 0 0 0 6.6 6.6l2.2-2.2a1 1 0 0 1 1-.25 11.4 11.4 0 0 0 3.6.57 1 1 0 0 1 1 1V20a1 1 0 0 1-1 1A17 17 0 0 1 3 4a1 1 0 0 1 1-1h3.5a1 1 0 0 1 1 1c0 1.25.2 2.450.57 3.57a1 1 0 0 1-.25 1z"/></svg>
      866-392-5074 US(TF)
      <span class="sep"></span>
      <svg viewBox="0 0 24 24" aria-hidden="true"><path d="M7 1h10a2 2 0 0 1 2 2v18a2 2 0 0 1-2 2H7a2 2 0 0 1-2-2V3a2 2 0 0 1 2-2zm0 4v13h10V5z"/></svg>
      123-456-3190
      <span class="sep"></span>
      <svg viewBox="0 0 24 24" aria-hidden="true"><path d="M2 5h20v14H2zm2 2v.5l8 5 8-5V7l-8 5z"/></svg>
      gpinfold@plavorix.com
    </p>
  </section>

</body>
</html>
```